Harvest Lantern Jamboree Announcement on a 6x9 Postcard

I would like a 6x9 postcard mailer inviting people to our Harvest Lantern Jamboree at Cedarlight Church in Milwaukee Wisconsin. The template is included

Some activities would include:
School Supply Giveaway
Free Food
Bounce Houses
Face Painting
and more....

Date/Time: Saturday August 17th from 2pm to 4pm

Side 2 would have our Logo (We do have the AI or EPS file if needed), Date, Name, Address, QR Code, phone, Website Information.
Saturday, August 17 from 2pm-4pm
Cedarlight Church
4815 W. 37th Street
Milwaukee, WI 53288
Ph: 414-555-0172
Website: www.cedarlightfc.example
tagline: A Home Where Welcomed Friends Welcome Friends

Target Market(s)

Neighborhoods immediately surrounding our church who have young children in need of school supplies.

Industry/Entity Type

Christian Church

Colors
0054AA
0677BA
7BADD7
CADEEF
E8F1F8
EB3D1F
EC4F4E
F09395
F8D3D4
FCEDEE

Requirements
Nice to have
• I would like to have a picture of our building with additional pictures on the back side with some of the activities we will have.

```html
<!DOCTYPE html>
<html lang="en">
<head>
<meta charset="utf-8">
<title>Harvest Lantern Jamboree Postcard</title>
<link rel="stylesheet" href="https://fonts.googleapis.com/css2?family=Allura&family=Bebas+Neue&family=Jost:wght@800&family=Montserrat:wght@300;500;600;800;900&family=Oswald:wght@200;600&family=Poppins:wght@400&display=swap">
<style>
  :root {
    --page: #dcdedd;
    --night-top: #1b1040;
    --night-bottom: #2e1129;
    --violet: #6b3ef2;
    --pink: #e0457e;
    --magenta: #e04ad8;
    --peach: #f8b16c;
    --red: #e4261c;
    --white: #ffffff;
    --leaf-deep: #0e4aa0;
    --leaf-teal: #2fb2d6;
    --paper: #ffffff;
  }
  * { margin: 0; padding: 0; box-sizing: border-box; }
  html, body { width: 857px; height: 1200px; overflow: hidden; }
  body { background: var(--page); position: relative; font-family: "Poppins", sans-serif; color: var(--white); }

  .card { position: absolute; left: 83px; width: 691px; height: 460px; overflow: hidden; }
  .card--front { top: 119px; background: linear-gradient(180deg, var(--night-top) 0%, #261046 55%, var(--night-bottom) 100%); }
  .card--back { top: 627px; background: var(--paper); }
  .back-panel {
    position: absolute; inset: 0;
    background: linear-gradient(180deg, var(--night-top) 0%, #27104a 50%, var(--night-bottom) 100%);
    clip-path: polygon(0 0, 573px 0, 573px 240px, 458px 240px, 458px 391px, 303px 391px, 303px 460px, 0 460px);
  }
  .abs { position: absolute; }

  .foliage { position: absolute; }
  .foliage--left { left: 0; top: 0; width: 227px; height: 153px;
    background: radial-gradient(ellipse at 20% 20%, var(--leaf-teal) 0%, var(--leaf-deep) 45%, transparent 75%); opacity: .85; }
  .foliage--right { right: 0; top: 0; width: 178px; height: 116px;
    background: radial-gradient(ellipse at 85% 15%, var(--leaf-teal) 0%, var(--leaf-deep) 45%, transparent 75%); opacity: .85; }

  .brand { display: flex; align-items: center; gap: 6px; font-family: "Montserrat", sans-serif; font-weight: 800; font-size: 22px; line-height: 1; color: var(--white); white-space: nowrap; }
  .brand__mark { width: 12px; height: 12px; background: var(--red); }
  .brand--front { left: 0; width: 691px; top: 62px; justify-content: center; }
  .brand--back { left: 268px; top: 244px; }

  .date { font-family: "Oswald", sans-serif; width: 100px; height: 120px; }
  .date > div { position: absolute; left: 0; line-height: 1; white-space: nowrap; }
  .date__day { font-weight: 200; font-size: 60px; letter-spacing: -1px; top: -10px; }
  .date__month { font-family: "Bebas Neue", sans-serif; color: var(--violet); font-size: 41px; top: 52px; }
  .date__weekday { font-weight: 200; font-size: 25px; top: 87px; letter-spacing: -.3px; }
  .date--front { left: 82px; top: 132px; }
  .date--back { left: 29px; top: 180px; }

  .time-box { border: 1px solid var(--white); display: flex; flex-direction: column; align-items: center; justify-content: center; font-family: "Jost", sans-serif; font-weight: 800; line-height: .95; }
  .time-box__to { font-family: "Allura", cursive; color: var(--pink); font-weight: 400; line-height: .6; }
  .time-box--front { left: 83px; top: 253px; width: 92px; height: 89px; font-size: 34px; }
  .time-box--front .time-box__to { font-size: 20px; }
  .time-box--back { left: 143px; top: 181px; width: 113px; height: 110px; font-size: 44px; }
  .time-box--back .time-box__to { font-size: 24px; }

  .welcome { left: 200px; top: 113px; font-family: "Allura", cursive; font-size: 46px; line-height: 1; white-space: nowrap; }
  .event-title { left: 202px; top: 0; font-family: "Montserrat", sans-serif; font-weight: 900; line-height: 1; }
  .event-title span { position: absolute; left: 0; display: block; background-clip: text; -webkit-background-clip: text; color: transparent; white-space: nowrap; }
  .event-title__l1 { top: 160px; font-size: 50px; background-image: linear-gradient(180deg, var(--magenta), var(--pink)); }
  .event-title__l2 { top: 220px; font-size: 50px; background-image: linear-gradient(180deg, var(--peach), var(--pink)); }
  .event-title__l3 { top: 285px; font-size: 44px; background-image: linear-gradient(180deg, var(--pink), #d23d6c); }

  .activities { left: 489px; top: 142px; width: 120px; }
  .activities__head { font-family: "Bebas Neue", sans-serif; font-weight: 400; font-size: 21px; line-height: .9; color: var(--violet); height: 46px; }
  .activities__list { list-style: none; border-top: 1px dashed rgba(255,255,255,.6); }
  .activities__list li { font-size: 13px; line-height: 1.22; padding: 8px 0; border-bottom: 1px dashed rgba(255,255,255,.6); white-space: nowrap; }
  .activities__list li:last-child { border-bottom: none; }

  .city-band { border: 1.5px solid var(--violet); display: flex; align-items: center; justify-content: center; font-family: "Montserrat", sans-serif; font-weight: 600; white-space: nowrap; }
  .city-band--front { left: 82px; top: 364px; width: 527px; height: 28px; font-size: 16px; letter-spacing: 5.6px; padding-left: 5.6px; }
  .city-band--back { left: 29px; top: 307px; width: 412px; height: 22px; font-size: 12.5px; letter-spacing: 3.9px; padding-left: 3.9px; }

  .site { font-family: "Montserrat", sans-serif; font-weight: 500; white-space: nowrap; line-height: 1; }
  .site--front { left: 0; width: 691px; top: 410px; text-align: center; font-size: 12px; letter-spacing: 3px; }
  .site--back { left: 29px; top: 410px; font-size: 13px; letter-spacing: 2.6px; }

  .photo { position: absolute; }
  .photo--building { left: 31px; top: 31px; width: 167px; height: 127px; background: linear-gradient(160deg, #c9cdd2 0%, #8a4f3c 50%, #4d7a3a 100%); }
  .photo--bounce { left: 205px; top: 31px; width: 85px; height: 127px; background: linear-gradient(170deg, #5c7a2e 0%, #e4b63d 55%, #d9463a 100%); }
  .photo--gathering { left: 296px; top: 30px; width: 108px; height: 61px; background: linear-gradient(160deg, #7fa95b 0%, #d79b6d 55%, #b34a3b 100%); }
  .photo--supplies { left: 296px; top: 95px; width: 108px; height: 63px; background: linear-gradient(160deg, #8e3b6e 0%, #2b7c8f 55%, #e2c43f 100%); }

  .tagline { left: 421px; top: 28px; width: 150px; white-space: nowrap; }
  .tagline span { display: block; height: 26.5px; line-height: 26.5px; }
  .tagline__lead { font-family: "Bebas Neue", sans-serif; font-size: 27px; color: var(--violet); }
  .tagline__soft { font-family: "Montserrat", sans-serif; font-weight: 300; font-size: 22px; color: var(--red); }
  .tagline__bold { font-family: "Montserrat", sans-serif; font-weight: 900; font-size: 24px; color: var(--white); }

  .contact-phone { left: 29px; top: 345px; display: flex; align-items: center; gap: 8px; font-family: "Oswald", sans-serif; font-weight: 600; font-size: 29px; line-height: 1; white-space: nowrap; }
  .icon-dot { width: 21px; height: 21px; border-radius: 50%; background: var(--violet); display: flex; align-items: center; justify-content: center; flex: none; }
  .contact-address { left: 253px; top: 343px; display: flex; gap: 9px; font-size: 15px; line-height: 1.2; white-space: nowrap; }
  .contact-address .icon-dot { width: 14px; height: 14px; margin-top: 3px; }
  .contact-address address { font-style: normal; }
  .divider { left: 29px; top: 391px; width: 251px; border-top: 1px dashed rgba(255,255,255,.55); }
</style>
</head>
<body>

  <section class="card card--front" aria-label="Postcard front">
    <div class="foliage foliage--left" role="img" aria-label="Tropical leaves in blue and teal"></div>
    <div class="foliage foliage--right" role="img" aria-label="Tropical leaves in blue and teal"></div>

    <div class="brand brand--front abs"><span class="brand__mark"></span>CEDARLIGHT</div>

    <div class="date date--front abs">
      <div class="date__day">17TH</div>
      <div class="date__month">AUGUST</div>
      <div class="date__weekday">SATURDAY</div>
    </div>
    <div class="time-box time-box--front abs">
      <span>2PM</span><span class="time-box__to">to</span><span>4PM</span>
    </div>

    <div class="welcome abs">Welcome to Our</div>
    <h1 class="event-title abs">
      <span class="event-title__l1">HARVEST</span>
      <span class="event-title__l2">LANTERN</span>
      <span class="event-title__l3">JAMBOREE</span>
    </h1>

    <div class="activities abs">
      <h2 class="activities__head">SOME ACTIVITIES<br>WOULD INCLUDE:</h2>
      <ul class="activities__list">
        <li>SCHOOL SUPPLY<br>GIVEAWAY</li>
        <li>FREE FOOD</li>
        <li>BOUNCE HOUSES</li>
        <li>FACE PAINTING<br>AND MORE....</li>
      </ul>
    </div>

    <div class="city-band city-band--front abs">CEDARLIGHT CHURCH IN MILWAUKEE</div>
    <div class="site site--front abs">www.cedarlightfc.example</div>
  </section>

  <section class="card card--back" aria-label="Postcard back">
    <div class="back-panel"></div>

    <div class="photo photo--building" role="img" aria-label="Photo of the church building"></div>
    <div class="photo photo--bounce" role="img" aria-label="Photo of a bounce house slide"></div>
    <div class="photo photo--gathering" role="img" aria-label="Photo of neighbours sharing food outdoors"></div>
    <div class="photo photo--supplies" role="img" aria-label="Photo of backpacks and school supplies"></div>

    <div class="tagline abs">
      <span class="tagline__lead">A HOME WHERE</span>
      <span class="tagline__soft">WELCOMED</span>
      <span class="tagline__soft">FRIENDS</span>
      <span class="tagline__bold">WELCOME</span>
      <span class="tagline__bold">FRIENDS</span>
    </div>

    <div class="date date--back abs">
      <div class="date__day">17TH</div>
      <div class="date__month">AUGUST</div>
      <div class="date__weekday">SATURDAY</div>
    </div>
    <div class="time-box time-box--back abs">
      <span>2PM</span><span class="time-box__to">to</span><span>4PM</span>
    </div>

    <div class="brand brand--back abs"><span class="brand__mark"></span>CEDARLIGHT</div>

    <div class="city-band city-band--back abs">CEDARLIGHT CHURCH IN MILWAUKEE</div>

    <div class="contact-phone abs">
      <span class="icon-dot">
        <svg width="12" height="12" viewBox="0 0 24 24" aria-hidden="true"><path fill="#fff" d="M6.6 10.8a15.1 15.1 0 0 0 6.6 6.6l2.2-2.2a1 1 0 0 1 1-.25 11.4 11.4 0 0 0 3.6.57 1 1 0 0 1 1 1V20a1 1 0 0 1-1 1A17 17 0 0 1 3 4a1 1 0 0 1 1-1h3.5a1 1 0 0 1 1 1c0 1.25.2 2.45.57 3.57a1 1 0 0 1-.25 1z"/></svg>
      </span>
      414-555-0172
    </div>

    <div class="contact-address abs">
      <span class="icon-dot">
        <svg width="8" height="8" viewBox="0 0 24 24" aria-hidden="true"><path fill="#fff" d="M2 5h20v14H2zM3.5 6.5 12 13l8.5-6.5v-.1h-17z"/></svg>
      </span>
      <address>4815 W. 37th Street<br>Milwaukee, WI 53288</address>
    </div>

    <div class="divider abs"></div>
    <div class="site site--back abs">www.cedarlightfc.example</div>
  </section>

</body>
</html>
```